Addiction Counselor Non-profit Needs Flyer Design Project - SAP

We need a flyer design for a non-profit organization based in Washington, DC called "TRELVIN, The Guild for Recovery Practitioners". TRELVIN, the Guild for Recovery Practitioners, represents the professional interests of more than 75,000 addiction counselors, educators and other addiction-focused health care professionals in the United States, Canada and abroad. TRELVIN’s members are addiction counselors, educators and other addiction-focused health care professionals, who specialize in addiction prevention, treatment, recovery support and education. An important part of the healthcare continuum, TRELVIN members and its 44 state affiliates work to create healthier individuals, families and communities through prevention, intervention, quality treatment and recovery support.

The purpose of the flyer is to sale this product and inform the addiction professional of ways to make more money by becoming a Substance Abuse Professional (SAP).

We would like to see designs that use blue, the main color of our website (www.trelvin-guild.example).

The final design should communicate professionalism and there is a great benefit to the individual for joining TRELVIN.
Updates

Hello - 

I have received several designs so far, but they are not focused enough on the product.  The main focus of this flyer should be on the SAP manual/course for purchase and MUST include an image of the product prominently.  Also note that the webinar logo is only a secondary mention item.  It should not be the focus of the page.  
Thanks to all who have submitted and who are planning to submit before the deadline!
Corla

Target Market(s)

Our membership potentials are professionals, mostly women and a few men, aged 23 to 65 who are all trained as therapists and care about people.

Industry/Entity Type

Non-Profit

Requirements
Must have
• The flyer can be one or two pages.
It must be easy to read.
Much contain Facebook, Twitter, and LinkedIn icons
Must have graphics - if a group of people, must be culturally diverse.
Must contain our logo - three are attached to choose from.
Must be clean and modern/contemporary in tone.
Must include the text that is in the attached Word document - FYI, there will be minor wording changes to the document prior to finalization but the basic structure and elements should still remain the same.

```html
<!DOCTYPE html>
<html lang="en">
<head>
<meta charset="utf-8">
<title>Earn the Substance Abuse Professional (SAP) Qualification</title>
<link href="https://fonts.googleapis.com/css2?family=Audiowide&family=Roboto+Condensed:ital,wght@0,300;0,400;0,700;1,300;1,400&display=swap" rel="stylesheet">
<style>
  :root {
    --blue-deep: #173f74;
    --blue-mid: #1f6aa8;
    --blue-light: #2f8fd0;
    --red: #b3121f;
    --heading-red: #a5121c;
    --ink: #2b2b2b;
    --ink-soft: #5a5a5a;
    --paper: #ffffff;
  }
  * { margin: 0; padding: 0; box-sizing: border-box; }
  html, body { width: 832px; height: 1200px; overflow: hidden; background: var(--paper); }
  .flyer {
    position: relative; width: 832px; height: 1200px; overflow: hidden;
    font-family: "Roboto Condensed", "Arial Narrow", sans-serif; color: var(--ink);
  }
  .masthead { position: absolute; left: 0; top: 0; width: 832px; height: 215px; }
  .masthead svg { position: absolute; inset: 0; }
  .title {
    position: absolute; color: #fff; font-family: "Audiowide", sans-serif;
    font-variant: small-caps; font-size: 37px; letter-spacing: 0.5px; line-height: 1;
    text-shadow: 1px 2px 3px rgba(0,0,0,0.35); white-space: nowrap;
  }
  .title-one { left: 54px; top: 46px; }
  .title-two { right: 54px; top: 108px; }
  .section-head {
    position: absolute; left: 38px; color: var(--heading-red);
    font-weight: 700; font-size: 17px; letter-spacing: 0.1px;
  }
  .lead { position: absolute; left: 38px; width: 750px; font-weight: 300; font-size: 15px; line-height: 20px; }
  .duties, .requirements {
    position: absolute; left: 38px; width: 750px; list-style: none;
    font-style: italic; font-weight: 300; color: var(--ink-soft);
  }
  .duties li, .requirements > li {
    position: relative; padding-left: 52px; font-size: 12px; line-height: 17px; margin-bottom: 8px;
  }
  .duties li::before, .requirements > li::before {
    content: "*"; position: absolute; left: 30px; top: 1px; font-style: normal;
  }
  .duties li:first-child { font-style: normal; }
  .requirements > li { margin-bottom: 6px; }
  .sublist { list-style: none; margin-top: 5px; }
  .sublist li {
    position: relative; padding-left: 24px; font-size: 11px; line-height: 15px; margin-bottom: 8px;
  }
  .sublist li::before { content: "•"; position: absolute; left: 5px; top: 0; font-style: normal; }
  .sublist.narrow li { padding-right: 0; }
  .photo {
    position: absolute; left: 570px; top: 826px; width: 215px; height: 142px;
    background: linear-gradient(135deg, #8d8f8c 0%, #b9b3a6 40%, #c99a66 75%, #a36f3c 100%);
  }
  .footer-band {
    position: absolute; left: 0; bottom: 0; width: 832px; height: 14px;
    background: linear-gradient(90deg, var(--blue-deep), var(--blue-light), var(--blue-deep));
  }
</style>
</head>
<body>
<main class="flyer">
  <header class="masthead">
    <svg width="832" height="215" viewBox="0 0 832 215" aria-hidden="true">
      <defs>
        <linearGradient id="skyBlue" x1="0" y1="0" x2="1" y2="1">
          <stop offset="0" stop-color="#14386a"/>
          <stop offset="0.55" stop-color="#1e64a2"/>
          <stop offset="1" stop-color="#2c8ccc"/>
        </linearGradient>
      </defs>
      <path d="M0,0 H832 V205 C600,200 420,175 250,128 C160,108 70,104 0,106 Z" fill="var(--red)"/>
      <path d="M0,0 H832 V184 C600,182 430,160 260,118 C170,100 80,94 0,95 Z" fill="url(#skyBlue)"/>
    </svg>
    <h1>
      <span class="title title-one">Earn the Substance Abuse Professional</span>
      <span class="title title-two">(SAP) Qualification</span>
    </h1>
  </header>

  <h2 class="section-head" style="top:182px">What is a Substance Abuse Professional?</h2>
  <p class="lead" style="top:223px">A U.S. Department of Transportation Substance Abuse Professional (SAP) operates as a “gatekeeper” of the return-to-duty process and provides an important service to the employee, the employer and the traveling public.</p>
  <p class="lead" style="top:275px">Specifically, Substance Abuse Professionals (SAPs) evaluate workers who have violated a U.S. Department of Transportation (DOT) drug and alcohol program regulation and make recommendations concerning education, treatment, follow-up testing and continuing care.</p>
  <p class="lead" style="top:349px">SAPs provide the following services for their clients:</p>

  <ul class="duties" style="top:382px">
    <li>Conduct comprehensive face-to-face assessment and clinical evaluation to determine what level of assistance the employee needs in resolving problems associated with alcohol use or prohibited drug use;</li>
    <li>Recommend a course of education and/or treatment with which the employee must comply prior to returning to DOT safety-sensitive duty;</li>
    <li>Serve as a referral source to assist the employee’s entry into an acceptable program;</li>
    <li>Conduct a face-to-face follow-up evaluation with the employee to determine if the individual has demonstrated successful compliance with recommendations of the initial evaluation and has made appropriate clinical progress sufficient to return to duty;</li>
    <li>Develop and direct a follow-up testing plan for the employee returning to work following successful compliance; and</li>
    <li>Provide the employee and employer with recommendations for continuing care.</li>
  </ul>

  <h2 class="section-head" style="top:586px">What are the requirements?</h2>
  <p class="lead" style="top:627px">In order to be an SAP, you need to have certain credentials, possess specific knowledge, receive training and achieve a passing score on an examination. There is also a continuing education requirement.</p>
  <p class="lead" style="top:681px">Each of these requirements is discussed below and is easily accomplished through TRELVIN’s Substance Abuse Professional’s U.S. DOT Alcohol and Drug Testing Regulation Qualification Independent Study Course.</p>

  <ul class="requirements" style="top:732px">
    <li>The applicant must have one of the following credentials:
      <ul class="sublist">
        <li>Alcohol and drug abuse counselor national level certification through the TRELVIN Certification Commission (NCC) or the International Credential &amp; Reciprocity Council (ICRX). Note: State level certification does NOT meet DOT requirements.</li>
        <li>Alcohol and drug abuse counselors with MAC certification through the National Board of Registered Counselors (NBRC)</li>
        <li>Licensed physician (Doctor of Medicine or Osteopathy)</li>
        <li>Licensed or certified psychologist</li>
        <li>Licensed or certified social worker</li>
        <li>Licensed or certified employee assistance professional (EAP)</li>
        <li>Licensed or certified Marriage and Family Therapist (MFT)</li>
      </ul>
    </li>
    <li>SAP applicants must possess knowledge of:
      <ul class="sublist">
        <li>Clinical experience in the diagnosis and treatment of substance abuse-related disorders.</li>
        <li>Understanding how the SAP role relates to the special responsibilities employers have for ensuring the safety of the traveling public.</li>
        <li>The nine required components laid out in Section 281 (c), Part 40 of the U.S. Department of Transportation’s agency regulations, SAP guidelines and any significant changes to the SAP guidelines.</li>
        <li>Note: Degrees and certificates alone do not confer to you these knowledge requirements.</li>
      </ul>
    </li>
    <li>SAP applicants must receive SAP training and pass a validated examination administered by a nationally recognized professional or training organization.</li>
    <li>SAPs must complete 12 hours of professional development relevant to performing SAP functions during each subsequent three-year renewal period.</li>
  </ul>

  <div class="photo" role="img" aria-label="Photo of a distressed woman resting her head in her hands at a table scattered with pills beside a glass of whiskey"></div>

  <footer class="footer-band" aria-hidden="true"></footer>
</main>
</body>
</html>
```